Web design project for exciting Australian start-up

Background
We are looking for a creative and talented web design artist to work alongside our market leading web developer.
• You will be required to create a modern and clean design theme for our website, incorporating selected rustic colour scheme elements for our exciting Australian start-up to operate within the coffee industry.
reoccurring work to be expected to flow to the successful designer.
Requirements
• c. 5 - 10 page website
• Landing page
• Log in/ out
• 404 template
• Typography is emphasised
• Please use either a) typemarrow.com, b) free web fonts, c) brindle fonts
• All design elements in vector format
• Preferably with icons for each header title(i.e. about us, how it works etc) but designer have free reign over how the site looks, so might not be applicable
• All pages to be responsive
• Down to eSlab resolution

High level visual design brief attached - additional pages to be worked from base design.

Design inspiration
• We would like to use design elements from the following sources:
http://www.zandrix.com/halcyon/ (Functionality)
Colour scheme refer to logo and complementary style guide

```html
<!DOCTYPE html>
<html lang="en">
<head>
<meta charset="utf-8">
<title>Joe Blogs Coffee Beans – Brewhaven</title>
<link href="https://fonts.googleapis.com/css2?family=Arimo:wght@400;700&family=Oswald:wght@400;500&display=swap" rel="stylesheet">
<style>
:root{
  --orange:#f7964a;
  --ink:#333333;
  --text:#555555;
  --muted:#666666;
  --bar:#4b4b49;
  --tab:#666664;
  --tab-active:#eeeeee;
  --line:#cfcfcf;
  --footer-bg:#f6f6f6;
  --base-bg:#2b2b2b;
  --star:#e5a21a;
  --star-off:#dddddd;
  --map:#e4e1da;
  --beans:#4a2614;
  --cup:#c9b8a6;
  --white:#ffffff;
}
*{box-sizing:border-box;margin:0;padding:0}
html,body{width:1200px;height:1057px;overflow:hidden;background:var(--white);font-family:"Arimo",Arial,sans-serif;color:var(--text)}
.page{position:relative;width:1200px;height:1057px}
.abs{position:absolute}

/* header */
.site-header{position:absolute;left:0;top:0;width:1200px;height:84px;border-bottom:3px solid var(--orange)}
.brand{position:absolute;left:131px;top:19px;display:flex;align-items:center;gap:10px;height:56px}
.brand-dot{width:40px;height:40px;border-radius:50%;background:var(--orange)}
.brand-name{font-weight:700;font-size:22px;letter-spacing:1px;color:var(--ink)}
.btn{position:absolute;top:22px;height:32px;width:70px;font-size:13px;color:var(--white);display:flex;align-items:center;justify-content:center;border-radius:2px}
.btn-login{left:918px;background:var(--orange)}
.btn-signup{left:998px;width:71px;background:var(--bar)}

/* profile */
.supplier-name{left:131px;top:120px;font-family:"Oswald",sans-serif;font-weight:400;font-size:25px;color:var(--orange);letter-spacing:-0.3px}
.supplier-meta{left:131px;font-size:13px;color:var(--ink)}
.review-count{right:131px;top:124px;font-weight:700;font-size:16px;color:var(--orange)}
.review-label{right:131px;top:154px;font-weight:700;font-size:15px;color:var(--orange)}
.member-since{right:131px;top:185px;font-size:13px;color:var(--ink)}

/* tabs panel */
.catalogue{left:131px;top:241px;width:630px;height:435px;border:1px solid var(--line)}
.tab-bar{position:absolute;left:0;top:0;width:100%;height:44px;background:var(--bar)}
.tab{position:absolute;top:9px;height:26px;font-size:13px;color:var(--white);display:flex;align-items:center;justify-content:center}
.tab::before{content:"";position:absolute;inset:0;background:var(--tab);transform:skewX(-20deg);z-index:0}
.tab span{position:relative;z-index:1}
.tab.active{color:var(--orange)}
.tab.active::before{background:var(--tab-active)}
.product-name{font-size:13px;color:var(--orange)}
.product-text{font-size:13px;line-height:19px;color:var(--text)}
.product-photo{width:98px;height:85px;border:1px solid #cccccc}
.photo-beans{background:var(--beans)}
.photo-cup{background:var(--cup)}
.spec{font-size:13px;color:var(--text)}

/* supply box */
.supply{left:806px;top:241px;width:263px;height:436px;border:2px solid var(--orange);border-radius:6px}
.supply-title{position:absolute;left:0;top:16px;width:100%;text-align:center;font-size:17px;font-weight:400;color:var(--ink)}
.supply-map{position:absolute;left:18px;top:46px;width:224px;height:183px;background:var(--map)}
.stat{position:absolute;left:18px;font-size:13px;color:#222222}
.stat-small{font-size:11px;color:var(--muted)}
.rating{position:absolute;left:18px;top:400px;display:flex;gap:5px}

/* footer */
.site-footer{position:absolute;left:0;top:735px;width:1200px;height:232px;background:var(--footer-bg)}
.footer-col{position:absolute;top:55px}
.footer-heading{display:flex;align-items:center;gap:4px;font-size:18px;font-weight:400;color:#444444;padding-bottom:6px;border-bottom:1px solid var(--orange);width:117px;white-space:nowrap}
.footer-heading .bean{width:20px;height:20px;border-radius:50%;background:var(--orange);flex:none}
.footer-list{list-style:none;margin-top:14px}
.footer-list li{font-size:14px;color:var(--muted);height:27px;display:flex;align-items:center;gap:5px}
.arrow{width:0;height:0;border-left:7px solid var(--orange);border-top:4px solid transparent;border-bottom:4px solid transparent}
.sq{width:7px;height:7px;background:var(--orange)}
.tweet{font-size:14px;line-height:27px;color:var(--muted);width:240px;padding-left:14px;position:relative;margin-top:14px}
.tweet::before{content:"";position:absolute;left:0;top:9px;width:9px;height:9px;border-radius:50%;background:#888888}
.base{position:absolute;left:0;top:967px;width:1200px;height:90px;background:var(--base-bg);color:var(--white);font-size:12px;text-align:center;padding-top:39px}
</style>
</head>
<body>
<div class="page">

  <header class="site-header">
    <div class="brand"><span class="brand-dot"></span><span class="brand-name">BREWHAVEN</span></div>
    <a class="btn btn-login">Login</a>
    <a class="btn btn-signup">Sign up</a>
  </header>

  <h1 class="abs supplier-name">JOE BLOGS COFFEE BEANS</h1>
  <p class="abs supplier-meta" style="top:162px">Melbourne, Australia</p>
  <p class="abs supplier-meta" style="top:183px">[Wholesaler description]</p>
  <p class="abs review-count">[10]</p>
  <p class="abs review-label">Reviews</p>
  <p class="abs member-since">Member since [Feb, 2014]</p>

  <section class="abs catalogue">
    <nav class="tab-bar">
      <div class="tab active" style="left:9px;width:92px"><span>Our Beans</span></div>
      <div class="tab" style="left:107px;width:93px"><span>Machinery</span></div>
      <div class="tab" style="left:200px;width:100px"><span>Accessories</span></div>
      <div class="tab" style="left:302px;width:78px"><span>Training</span></div>
      <div class="tab" style="left:376px;width:94px"><span>Promotions</span></div>
    </nav>

    <article>
      <p class="abs product-name" style="left:21px;top:66px">Coffee bean XX</p>
      <p class="abs product-text" style="left:21px;top:93px">The blend<br>[Insert blend description]</p>
      <div class="abs product-photo photo-beans" style="left:184px;top:66px" role="img" aria-label="Photo of roasted coffee beans"></div>
      <p class="abs spec" style="left:22px;top:375px">Origin:</p>
      <p class="abs spec" style="left:160px;top:375px">[xx]</p>
      <p class="abs spec" style="left:22px;top:399px">Grind availability:</p>
      <p class="abs spec" style="left:160px;top:399px">[xx]</p>
    </article>

    <article>
      <p class="abs product-name" style="left:335px;top:66px">Coffee bean XX</p>
      <p class="abs product-text" style="left:335px;top:93px">The blend<br>[Insert blend description]</p>
      <div class="abs product-photo photo-cup" style="left:498px;top:66px" role="img" aria-label="Photo of a cup of coffee"></div>
      <p class="abs spec" style="left:337px;top:375px">Origin:</p>
      <p class="abs spec" style="left:475px;top:375px">[xx]</p>
      <p class="abs spec" style="left:337px;top:399px">Grind availability:</p>
      <p class="abs spec" style="left:475px;top:399px">[xx]</p>
    </article>
  </section>

  <aside class="abs supply">
    <h2 class="supply-title">Where we currently supply</h2>
    <div class="supply-map" role="img" aria-label="Map of the supply area"></div>
    <p class="stat" style="top:250px">Tender response rate</p>
    <p class="stat" style="top:271px">[x]%</p>
    <p class="stat" style="top:306px">Tender response time</p>
    <p class="stat stat-small" style="top:326px">[Within a few days]</p>
    <p class="stat" style="top:365px">Wholesaler’s overall customer rating</p>
    <div class="rating" aria-label="3 out of 5 stars">
      <svg width="20" height="20" viewBox="0 0 24 24"><path fill="var(--star)" d="M12 1l3.1 7.3 7.9.6-6 5.2 1.9 7.7L12 17.8 5.1 21.8 7 14.1 1 8.9l7.9-.6z"/></svg>
      <svg width="20" height="20" viewBox="0 0 24 24"><path fill="var(--star)" d="M12 1l3.1 7.3 7.9.6-6 5.2 1.9 7.7L12 17.8 5.1 21.8 7 14.1 1 8.9l7.9-.6z"/></svg>
      <svg width="20" height="20" viewBox="0 0 24 24"><path fill="var(--star)" d="M12 1l3.1 7.3 7.9.6-6 5.2 1.9 7.7L12 17.8 5.1 21.8 7 14.1 1 8.9l7.9-.6z"/></svg>
      <svg width="20" height="20" viewBox="0 0 24 24"><path fill="var(--star-off)" d="M12 1l3.1 7.3 7.9.6-6 5.2 1.9 7.7L12 17.8 5.1 21.8 7 14.1 1 8.9l7.9-.6z"/></svg>
      <svg width="20" height="20" viewBox="0 0 24 24"><path fill="var(--star-off)" d="M12 1l3.1 7.3 7.9.6-6 5.2 1.9 7.7L12 17.8 5.1 21.8 7 14.1 1 8.9l7.9-.6z"/></svg>
    </div>
  </aside>

  <footer class="site-footer">
    <div class="footer-col" style="left:131px">
      <h3 class="footer-heading"><span class="bean"></span>Helpful Info</h3>
      <ul class="footer-list">
        <li><span class="arrow"></span>About us</li>
        <li><span class="arrow"></span>Media enquiries</li>
        <li><span class="arrow"></span>Terms &amp; conditions</li>
        <li><span class="arrow"></span>Privacy policy</li>
      </ul>
    </div>
    <div class="footer-col" style="left:363px">
      <h3 class="footer-heading" style="width:131px"><span class="bean"></span>Who we are?</h3>
      <ul class="footer-list">
        <li><span class="arrow"></span>How it works</li>
        <li><span class="arrow"></span>FAQ</li>
        <li><span class="arrow"></span>Contact us</li>
      </ul>
    </div>
    <div class="footer-col" style="left:598px">
      <h3 class="footer-heading" style="width:133px"><span class="bean"></span>Tweets</h3>
      <p class="tweet">Nasagni doloresqui ratione volu em sequi nescique porro quisquam est qui dolorem ipsumquia<br>3-03-2014</p>
    </div>
    <div class="footer-col" style="left:889px">
      <h3 class="footer-heading" style="width:131px"><span class="bean"></span>Join us on</h3>
      <ul class="footer-list">
        <li><span class="sq"></span>Friendwall</li>
        <li><span class="sq"></span>Chirpline</li>
        <li><span class="sq"></span>Proconnect</li>
        <li><span class="sq"></span>Cliptube</li>
      </ul>
    </div>
  </footer>

  <div class="base">Copyright © 2014 Brewhaven</div>
</div>
</body>
</html>
```